Request for Business Card Design

Hi. My name is Marlene, I am looking for a new business card design for my company, Quarrow Signal Instruments, LLC. I really like the design you did for Tarsel Venture and was hoping you could do something similar using our full logo and our mark. I am also open to any raised texture design using our mark. I have attached our full logo, which would need to be somewhere on the card, as well as the mark in both outline and full form, as well as our brand colors / guide. The card does not have to be white, as long as our logo and mark appear. I actually like darker colored business cards more, but am open to all options. If you are interested in working with me, please let me know. We would also take the business card design into letterhead design if you can do that.

```html
<!DOCTYPE html>
<html lang="en">
<head>
<meta charset="utf-8">
<title>Quarrow Signal Instruments — Business Card</title>
<link rel="stylesheet" href="https://fonts.googleapis.com/css2?family=Open+Sans:wght@400;600;700;800&display=swap">
<style>
  :root {
    --bg: #232323;
    --card: #3f3f41;
    --card-edge: #1a9ac4;
    --accent: #1a9ac4;
    --deboss: #1c1c1d;
    --ink: #ffffff;
  }
  * { box-sizing: border-box; margin: 0; padding: 0; }
  html, body { width: 1200px; height: 780px; overflow: hidden; }
  body {
    background: var(--bg);
    font-family: "Open Sans", Arial, sans-serif;
    display: flex;
    align-items: center;
    justify-content: center;
    gap: 40px;
  }
  .card {
    position: relative;
    width: 540px;
    height: 310px;
    background: var(--card);
    border-radius: 18px;
    border-bottom: 4px solid var(--card-edge);
    overflow: hidden;
  }

  /* Front */
  .card--front { display: flex; align-items: center; justify-content: center; gap: 16px; }
  .front-dot {
    width: 46px; height: 46px; border-radius: 50%;
    background: var(--deboss);
  }
  .front-name {
    color: var(--deboss);
    font-weight: 800;
    font-size: 30px;
    line-height: 1.05;
    text-transform: uppercase;
    letter-spacing: 0.5px;
  }

  /* Back */
  .mark-circle {
    position: absolute;
    left: 62px; top: 70px;
    width: 150px; height: 150px;
    border: 3px solid var(--accent);
    border-radius: 50%;
  }
  .divider {
    position: absolute;
    left: 262px; top: 40px;
    width: 2px; height: 180px;
    background: var(--ink);
  }
  .contact {
    position: absolute;
    left: 290px; top: 44px;
    color: var(--ink);
  }
  .contact__name {
    color: var(--accent);
    font-weight: 800;
    font-size: 38px;
    line-height: 1;
  }
  .contact__role {
    font-weight: 600;
    font-size: 15px;
    margin: 2px 0 16px 6px;
  }
  .contact__list { list-style: none; font-size: 13px; line-height: 1.65; }
  .contact__list li { display: flex; align-items: center; gap: 9px; }
  .contact__list svg { width: 13px; height: 13px; fill: var(--accent); flex: none; }
  .address-band {
    position: absolute;
    left: 0; right: 0; bottom: 20px;
    height: 36px;
    background: var(--accent);
    color: var(--ink);
    font-size: 15px;
    font-weight: 400;
    display: flex; align-items: center; justify-content: center;
  }
</style>
</head>
<body>
  <section class="card card--front" aria-label="Card front">
    <span class="front-dot"></span>
    <p class="front-name">Quarrow Signal<br>Instruments</p>
  </section>

  <section class="card card--back" aria-label="Card back">
    <span class="mark-circle"></span>
    <span class="divider"></span>
    <div class="contact">
      <h1 class="contact__name">Marlene</h1>
      <p class="contact__role">Director</p>
      <ul class="contact__list">
        <li><svg viewBox="0 0 24 24"><path d="M6.6 10.8a15 15 0 0 0 6.6 6.6l2.2-2.2c.3-.3.7-.4 1-.2 1.1.4 2.3.6 3.6.6.6 0 1 .4 1 1V20c0 .6-.4 1-1 1A17 17 0 0 1 3 4c0-.6.4-1 1-1h3.5c.6 0 1 .4 1 1 0 1.3.2 2.5.6 3.6.1.3 0 .7-.2 1z"/></svg>+001 555 218 4410</li>
        <li><svg viewBox="0 0 24 24"><path d="M6 2h9l3 3v5h2a2 2 0 0 1 2 2v8a2 2 0 0 1-2 2H4a2 2 0 0 1-2-2v-8a2 2 0 0 1 2-2h2zm2 2v6h8V6h-2V4zm0 11h8v2H8z"/></svg>+001 555 218 4477</li>
        <li><svg viewBox="0 0 24 24"><path d="M12 2a10 10 0 1 0 0 20 10 10 0 0 0 0-20zm-1 17.9A8 8 0 0 1 4.1 11H8c.1 3.2 1.2 6.3 3 8.9zM8 9H4.1A8 8 0 0 1 11 4.1 16 16 0 0 0 8 9zm2 0c.3-2.4 1-4.4 2-6 1 1.6 1.7 3.6 2 6zm0 2h4c-.2 2.9-1 5.4-2 7-1-1.6-1.8-4.1-2-7zm6 0h3.9a8 8 0 0 1-6.9 6.9c1.8-2.6 2.9-5.7 3-6.9zm0-2c-.3-1.9-1-3.5-3-4.9A8 8 0 0 1 19.9 9z"/></svg>www.quarrowsignal.com</li>
        <li><svg viewBox="0 0 24 24"><path d="M3 5h18a1 1 0 0 1 1 1v12a1 1 0 0 1-1 1H3a1 1 0 0 1-1-1V6a1 1 0 0 1 1-1zm1 2.4V17h16V7.4l-8 5.3z"/></svg>info@quarrowsignal.com</li>
      </ul>
    </div>
    <p class="address-band">1180 Halden Park Road • Brightwell, CO 80999</p>
  </section>
</body>
</html>
```